KRV Business Card

Looking for a business card for my restaurant group I own. Four different concepts:

Copperfield Alehouse
Bristow Alehouse
Tanager's Stone Hearth Kitchen
Pellston Patty Company

Card doesn't need to include all the logos.

```html
<!DOCTYPE html>
<html lang="en">
<head>
<meta charset="utf-8">
<title>KRV Business Card</title>
<link href="https://fonts.googleapis.com/css2?family=Open+Sans:wght@400;600;700&display=swap" rel="stylesheet">
<style>
  :root {
    --backdrop: #2b2c2e;
    --card: #141414;
    --gold: #d6b26a;
    --white: #f4f4f4;
    --grey: #8a8a8c;
  }
  * { margin: 0; padding: 0; box-sizing: border-box; }
  html, body {
    width: 1200px; height: 900px; overflow: hidden;
    background: var(--backdrop);
    font-family: "Open Sans", Arial, sans-serif;
  }
  .stage {
    position: relative; width: 1200px; height: 900px;
  }
  .card {
    position: absolute; left: 320px;
    width: 560px; height: 320px;
    background: var(--card);
    box-shadow: 0 18px 40px rgba(0,0,0,.45);
    display: flex; flex-direction: column; align-items: center; justify-content: center;
    text-align: center;
  }
  .card--front { top: 100px; }
  .card--back { top: 480px; }

  .brand {
    display: flex; align-items: center; gap: 12px;
    color: var(--gold); font-weight: 600;
    letter-spacing: 0.08em; text-transform: uppercase;
  }
  .brand__mark { background: var(--gold); }
  .card--front .brand { font-size: 30px; }
  .card--front .brand__mark { width: 22px; height: 22px; }
  .card--back .brand { font-size: 15px; gap: 8px; }
  .card--back .brand__mark { width: 12px; height: 12px; }

  .company {
    margin-top: 12px; color: var(--white);
    font-size: 21px; font-weight: 400;
  }
  .person {
    margin-top: 6px; color: var(--gold);
    font-size: 20px; font-weight: 700;
  }
  .rule {
    margin-top: 8px; width: 34px; height: 3px; background: var(--gold);
  }
  .icons {
    display: flex; gap: 10px; margin-top: 12px;
  }
  .icon { width: 20px; height: 20px; }
  .contact {
    margin-top: 10px; list-style: none;
    color: var(--white); font-size: 14px; line-height: 1.55;
  }
</style>
</head>
<body>
<main class="stage">
  <section class="card card--front" aria-label="Card front">
    <div class="brand"><span class="brand__mark"></span>Kestrel Ridge Ventures</div>
  </section>

  <section class="card card--back" aria-label="Card back">
    <div class="brand"><span class="brand__mark"></span>Kestrel Ridge Ventures</div>
    <p class="company">Kestrel Ridge Ventures</p>
    <p class="person">Dana Holloway</p>
    <div class="rule"></div>
    <div class="icons">
      <svg class="icon" viewBox="0 0 20 20" aria-label="Phone">
        <circle cx="10" cy="10" r="9" fill="none" stroke="#d6b26a" stroke-width="1.2"/>
        <path d="M7 5.5l1.6 2.4-1 1c.6 1.3 1.4 2.1 2.6 2.6l1-1 2.3 1.6-.9 1.6c-3.4-.3-6-2.9-6.4-6.4z" fill="#d6b26a"/>
      </svg>
      <svg class="icon" viewBox="0 0 20 20" aria-label="Email">
        <circle cx="10" cy="10" r="9" fill="none" stroke="#d6b26a" stroke-width="1.2"/>
        <rect x="5.5" y="6.8" width="9" height="6.4" fill="none" stroke="#d6b26a" stroke-width="1.2"/>
        <path d="M5.5 7l4.5 3.4L14.5 7" fill="none" stroke="#d6b26a" stroke-width="1.2"/>
      </svg>
      <svg class="icon" viewBox="0 0 20 20" aria-label="Website">
        <circle cx="10" cy="10" r="9" fill="none" stroke="#d6b26a" stroke-width="1.2"/>
        <circle cx="10" cy="10" r="4.6" fill="none" stroke="#d6b26a" stroke-width="1.1"/>
        <path d="M5.4 10h9.2M10 5.4c-2 2.6-2 6.6 0 9.2M10 5.4c2 2.6 2 6.6 0 9.2" fill="none" stroke="#d6b26a" stroke-width="1"/>
      </svg>
    </div>
    <ul class="contact">
      <li>555-210-4417</li>
      <li>dana@krvdining.com</li>
      <li>www.krvdining.com</li>
    </ul>
  </section>
</main>
</body>
</html>
```